Keystone Trench Co Business Card*

Looking for a professional, clean and crisp business card

I am in the underground utilities industry and am just looking for a really impressive business card. I would like our card to be white with our symbol crisp and clear with it protruding. I also have a business partner that will require his name and info on the card once the design is set. I would like to have our website info on the card which is;
http://keystonetrenchco.example/

Contact Information for Business Card

Website, contact name, number and email

```html
<!DOCTYPE html>
<html lang="en">
<head>
<meta charset="utf-8">
<title>Keystone Trench Co Business Card</title>
<link href="https://fonts.googleapis.com/css2?family=Montserrat:wght@800&family=Open+Sans:wght@400;600&display=swap" rel="stylesheet">
<style>
:root{
  --stage:#2b2b2b;
  --card-dark:#1e1e1e;
  --card-light:#ffffff;
  --brand-blue:#3a5ea8;
  --ink:#1a1a1a;
  --accent-red:#e0262b;
  --silver:#d9d9d9;
}
*{margin:0;padding:0;box-sizing:border-box}
html,body{width:1200px;height:895px;overflow:hidden;background:var(--stage)}
.canvas{position:relative;width:1200px;height:895px;font-family:"Open Sans",Arial,sans-serif}
.card{position:absolute;width:560px;height:320px;overflow:hidden;box-shadow:0 10px 30px rgba(0,0,0,.5)}
.card--back{left:110px;top:70px;background:var(--card-dark);border-bottom:6px solid var(--brand-blue)}
.card--front{left:530px;top:470px;background:var(--card-light)}
.wordmark{position:absolute;display:flex;align-items:center;gap:10px;font-family:"Montserrat",Arial,sans-serif;font-weight:800;font-size:26px;letter-spacing:.5px;white-space:nowrap}
.wordmark__dot{width:22px;height:22px;border-radius:50%}
.card--back .wordmark{left:50%;top:112px;transform:translateX(-50%);color:var(--silver)}
.card--back .wordmark__dot{background:var(--silver)}
.back-url{position:absolute;left:0;right:0;bottom:22px;text-align:center;color:#fff;font-size:13px;letter-spacing:1.5px}
.card--front .wordmark{left:50%;top:62px;transform:translateX(-50%);color:var(--ink)}
.card--front .wordmark__dot{background:var(--brand-blue)}
.contact-list{position:absolute;right:300px;top:150px;list-style:none;text-align:right;font-size:13px;color:var(--ink);line-height:22px}
.contact-list li{display:flex;justify-content:flex-end;align-items:center;gap:8px;white-space:nowrap}
.contact-list svg{width:12px;height:12px;flex:none}
.divider{position:absolute;left:275px;top:150px;width:1px;height:66px;background:var(--ink)}
.person{position:absolute;left:292px;top:156px}
.person__name{font-family:"Montserrat",Arial,sans-serif;font-weight:800;font-size:22px;color:var(--brand-blue);letter-spacing:1px;text-transform:uppercase}
.person__role{font-size:13px;color:var(--ink);margin-top:2px}
.address-band{position:absolute;left:0;right:0;bottom:18px;height:34px;background:var(--brand-blue);color:#fff;font-size:13px;display:flex;align-items:center;justify-content:center;letter-spacing:.4px}
</style>
</head>
<body>
<main class="canvas">
  <section class="card card--back" aria-label="Card back">
    <div class="wordmark"><span class="wordmark__dot"></span>Keystone Trench Co</div>
    <p class="back-url">www.keystonetrenchco.example</p>
  </section>

  <section class="card card--front" aria-label="Card front">
    <div class="wordmark"><span class="wordmark__dot"></span>Keystone Trench Co</div>

    <ul class="contact-list">
      <li>555-014-2290
        <svg viewBox="0 0 12 12" aria-hidden="true"><path d="M2.5 1l2 2.2-1 1.3c.7 1.5 1.8 2.6 3.2 3.2l1.3-1 2.2 2-1.3 1.6C5.6 10 2 6.4 1 2.4z" fill="var(--accent-red)"/></svg>
      </li>
      <li>dale@keystonetrenchco.example
        <svg viewBox="0 0 12 12" aria-hidden="true"><rect x="1" y="2.5" width="10" height="7" fill="none" stroke="var(--accent-red)" stroke-width="1.2"/><path d="M1 2.5l5 4 5-4" fill="none" stroke="var(--accent-red)" stroke-width="1.2"/></svg>
      </li>
      <li>www.keystonetrenchco.example
        <svg viewBox="0 0 12 12" aria-hidden="true"><g fill="none" stroke="var(--accent-red)" stroke-width="1"><circle cx="6" cy="6" r="5"/><ellipse cx="6" cy="6" rx="2.2" ry="5"/><path d="M1 6h10M2 3.5h8M2 8.5h8"/></g></svg>
      </li>
    </ul>

    <div class="divider"></div>

    <div class="person">
      <p class="person__name">Dale Marrow</p>
      <p class="person__role">Owner</p>
    </div>

    <div class="address-band">Keystone Trench Co Inc., 18 Alder Row, Brook Falls, CA 00000</div>
  </section>
</main>
</body>
</html>
```